Lotstallmart.com Webpage Design

Design Brief for lotstallmart.com (Copy of Brief also in attached Word file)

Name of Website- lotstallmart.com (existing logo and look & feel of website to be changed)

Logo - Finalised. The logo files are attached with the brief as “logo.jpeg”. The “Blue- Grey” version of the logo is for use on lighter backgrounds and the “Orange-White” version of the logo is for use on darker backgrounds. (A full Black version of the logo is also attached). Both versions may be used in different parts of the website. All attached files are in .png format.
Status - The website in functional and is undergoing user trials. However, we want to improve the look & feel of the website so at it seems
a. cotemporary,
b. Easy to Navigate
c. professional and
d. Vibrant.

Please visit ‘lotstallmart.com’ to check out the website and its functionalities – please use it only as a reference for the features & functions to be provided, however the designer should use a ‘Free Hand’ in designing the composition of various parts of the webpage without getting too influenced by the existing design

Objective of the Website ‘lotstallmart.com –
a. It is a portal focussed on listing of ‘Retail’ specific real-estate properties by developers, owners and realty brokers. The properties shall listed under the following four categories-
i. Retail Malls
ii. Shopping Complexes
iii. High-street shops
iv. Retail Warehouses
*refer lotstallmart.com for better clarity

b. The abovementioned properties shall be listed either for ‘Sale’ or ‘rent\lease’ or both

c. Users shall visit the site in case they wish to acquire a retail \ shop space either on ‘sale’ or ‘rent’. These Users would be able to specify the ‘Search Criteria’ through the tool-bars provided on the website – the ‘Search Criteria’ shall comprise of ‘Type of space category’, ‘City’, ‘Locality’, transaction type ie ‘Rent \ Sale’ and ‘Area Range’

d. The main revenue model for the website shall be listing fee ( or advertising charges ) payable by those listing their properties on the website.

Three Main Pages of Website (lotstallmart.com) that need to be designed -
a. Main Home Page (visit the web link - http://lotstallmart.com/ ) - The main home page has the “Search Toolbar” for specifying of Search Criteria by the User. It shall also have the following features & functions-
i. Main Advertising Banner
ii. Featured Projects
iii. New Launches
iv. Toolbar with buttons – ‘Advertise with Us’, ‘Listings Alert’, ‘Mart Wizards’, ‘Advertiser Login’

b. Property Listings Page (visit the web link - http://lotstallmart.com/gurgaon-in-india ) - The List of property options that match the Criteria specified by the ‘User’ get displayed on this page.

c. Property Detail Page - When the ‘User’ clicks on the “More….” Button on the ‘Property Listings Page’ (given in point b. above) the web page with the details of the property opens. (For Example – visit the web link - http://lotstallmart.com/vorne-Shopping-Complex-vorne-quadrion-gurgaon-636 )

Note:- Please refer to attached ‘Shopping’ related images the designer may use them on the website to provide a look & feel of retail if required – either separately or rotate in a single window

Target Market(s)

Retailers & Investors looking for retail space, Real Estate Brokers, Developers

Industry/Entity Type

Advertising

Number of Pages Required

3 page

Requirements
Must have
• Refer to existing site lotstallmart.com -- all the existing functionalities are a must have.
Nice to have
• The Designer may use the retail related images on the website if required for making it more vibrant. Refer attached images Shopping(1-6).jpg

```html
<!DOCTYPE html>
<html lang="en">
<head>
<meta charset="utf-8">
<title>Lotstallmart.com — Home</title>
<link href="https://fonts.googleapis.com/css2?family=Open+Sans:wght@400;600;700&display=swap" rel="stylesheet">
<style>
:root{
  --blue:#1196e6;
  --blue-deep:#0b79d0;
  --blue-head:#1a7fc9;
  --orange:#eea43a;
  --sky:#e4f2fb;
  --ink:#333;
  --muted:#888;
  --panel:#4a4a4a;
  --white:#fff;
}
*{box-sizing:border-box;margin:0;padding:0}
html,body{width:1200px;height:2632px;overflow:hidden}
body{font-family:"Open Sans",Arial,sans-serif;color:var(--ink);background:var(--white);position:relative;font-size:14px}
.abs{position:absolute}
section,header,footer,nav{position:absolute;left:0;width:1200px}

/* city bar */
.city-bar{top:0;height:39px;background:var(--blue);display:flex;justify-content:center;align-items:center;gap:26px;color:var(--white);font-size:15px}

/* header */
.site-header{top:39px;height:108px;background:var(--white)}
.brand{display:flex;align-items:center;gap:10px;font-weight:700;font-size:34px;color:var(--blue-deep)}
.brand .dot{width:36px;height:36px;border-radius:50%;background:var(--orange)}
.nav-item{font-size:13px;line-height:16px;color:var(--ink)}
.nav-item span{display:block;color:var(--blue)}
.btn{display:inline-flex;align-items:center;justify-content:center;background:var(--orange);color:var(--white);font-weight:600;border-radius:2px}
.small{font-size:12px}

/* hero */
.hero{top:147px;height:548px;background:linear-gradient(180deg,#3b2a1e 0%,#7a5a3a 40%,#4a3525 75%,#241a14 100%)}
.search-panel{left:784px;top:90px;width:305px;height:384px;background:var(--white);box-shadow:0 2px 8px rgba(0,0,0,.3)}
.search-head{height:45px;background:var(--orange);color:var(--white);font-size:20px;display:flex;align-items:center;gap:10px;padding-left:18px}
.search-body{padding:10px 14px}
.checks{display:grid;grid-template-columns:1fr 1fr;gap:6px 8px;font-size:12px;margin-bottom:8px}
.checks label{display:flex;align-items:center;gap:6px}
.checks i{width:12px;height:12px;border:1px solid #aaa;display:inline-block}
.field-label{font-size:13px;font-weight:600;margin:8px 0 4px}
.select{height:28px;border:1px solid #bbb;border-radius:2px;font-size:12px;color:#888;display:flex;align-items:center;padding-left:8px;position:relative}
.select svg{position:absolute;right:6px;top:9px}
.search-btn{width:100px;height:34px;font-size:18px;margin:12px auto 0;display:flex}

/* categories */
.categories{top:695px;height:193px}
.cat{width:230px}
.cat .icon{width:49px;height:49px;border-radius:50%;background:var(--blue);display:flex;align-items:center;justify-content:center;flex:none}
.cat h3{font-size:14px;font-weight:400;text-transform:uppercase;color:#222;margin-bottom:4px}
.cat p{font-size:13px;line-height:22px;color:#444;width:170px}

/* featured */
.featured{background:var(--sky)}
.featured.white{background:var(--white)}
.sec-title{font-size:25px;color:var(--blue-head);font-weight:400}
.sec-title small{font-size:14px;color:#555}
.card{width:280px}
.card .photo{width:280px;height:190px;position:relative}
.tag{position:absolute;right:0;color:var(--white);font-size:13px;padding:0 8px;height:30px;display:flex;align-items:center}
.tag.deal{top:10px;background:var(--orange)}
.tag.kind{top:51px;background:var(--blue)}
.card h4{font-size:25px;font-weight:400;color:var(--blue-head);margin-top:10px}
.card .place{font-size:14px;margin-top:4px}
.card .row{display:flex;justify-content:space-between;font-size:14px;color:var(--muted);margin-top:4px;padding-bottom:10px;border-bottom:2px solid #cfd8de}
.card .row b{font-weight:400;color:#222}
.card .foot{display:flex;justify-content:space-between;align-items:center;margin-top:18px}
.price{font-size:20px;color:var(--blue-deep)}
.card .btn{width:140px;height:33px;font-size:14px}
.arrow{width:30px;height:30px;border-radius:50%;background:var(--white);border:1px solid #444;display:flex;align-items:center;justify-content:center}

/* lower band */
.lower{top:1863px;height:391px;background:var(--sky)}
.col-title{font-size:25px;color:var(--blue-head);font-weight:400;padding-bottom:6px;border-bottom:1px solid #bcd3e3}
.input{height:28px;background:var(--white);border:1px solid #ccc;font-size:13px;color:#555;display:flex;align-items:center;padding-left:8px;position:relative}
.note{font-size:13px;color:#333}
.wizard-panel{left:772px;top:26px;width:317px;height:344px;background:var(--panel);color:var(--white);padding:14px 16px}
.wizard-panel h2{font-size:25px;font-weight:400;padding-bottom:8px;border-bottom:1px solid #777}
.wizard-panel p{font-size:12px;line-height:19px;margin:10px 0 12px}
.wizard-panel .input{margin-bottom:16px;height:27px}

/* footer */
.site-footer{top:2254px;height:378px;background:var(--blue-deep);color:var(--white)}
.foot-title{font-size:20px;font-weight:700}
.site-footer ul{list-style:none;font-size:14px}
.site-footer li::before{content:"\25B8  ";font-size:11px}
.foot-text{font-size:12.5px;line-height:19px;width:340px}
.contact p{font-size:13px;line-height:19px;margin-bottom:20px;display:flex;gap:8px;align-items:center}
.copy{font-size:12px}
.foot-brand{color:var(--white)}
</style>
</head>
<body>

<nav class="city-bar">
  <span>Bangalore</span><span>Chennai</span><span>Greater Noida</span><span>Gurgaon</span><span>Hyderabad</span><span>Jaipur</span><span>Khanna</span><span>Mumbai</span><span>Noida</span><span>Pune</span><span>Surat</span>
</nav>

<header class="site-header">
  <div class="brand abs" style="left:112px;top:32px"><span class="dot"></span>lotstallmart</div>
  <svg class="abs" style="left:500px;top:44px" width="24" height="22" viewBox="0 0 24 22"><path d="M2 11 12 2l10 9M5 9v11h14V9" fill="none" stroke="#555" stroke-width="2"/></svg>
  <div class="nav-item abs" style="left:546px;top:42px">Advertise with us<span>Standard listing Free</span></div>
  <div class="nav-item abs" style="left:686px;top:42px">Mart Wizards<span>Shop Search Services</span></div>
  <div class="nav-item abs" style="left:852px;top:47px">Listing Alert</div>
  <div class="small abs" style="left:950px;top:21px">List Your Property Here</div>
  <div class="btn abs" style="left:947px;top:42px;width:141px;height:31px;font-size:13px">Advertiser Login</div>
  <div class="small abs" style="left:944px;top:76px">New Advertiser - Register</div>
</header>

<section class="hero" role="img" aria-label="Family walking with shopping bags through a lit shopping mall at night">
  <div class="search-panel abs" role="search">
    <div class="search-head">
      <svg width="18" height="18" viewBox="0 0 18 18"><circle cx="7" cy="7" r="5.5" fill="none" stroke="#fff" stroke-width="2.5"/><path d="M11 11l5 5" stroke="#fff" stroke-width="2.5"/></svg>
      Property Search
    </div>
    <div class="search-body">
      <div class="checks">
        <label><i></i>Retail Malls</label><label><i></i>Shopping Complex</label>
        <label><i></i>High street Rehops</label><label><i></i>Retail Warehouses</label>
      </div>
      <div class="field-label">Sale Or Rent Or Both:</div>
      <div class="select">Both<svg width="10" height="7"><path d="M0 0h10L5 7z" fill="#444"/></svg></div>
      <div class="field-label">Select City:</div>
      <div class="select">--Select--<svg width="10" height="7"><path d="M0 0h10L5 7z" fill="#444"/></svg></div>
      <div class="field-label">Select Locality/Micro-Market.</div>
      <div class="select">--Select--<svg width="10" height="7"><path d="M0 0h10L5 7z" fill="#444"/></svg></div>
      <div class="field-label">Enter Keywords:</div>
      <div class="select">Name of Project, Developer etc<svg width="10" height="7"><path d="M0 0h10L5 7z" fill="#444"/></svg></div>
      <div class="btn search-btn">Search</div>
    </div>
  </div>
</section>

<section class="categories">
  <div class="cat abs" style="left:112px;top:38px;display:flex;gap:18px">
    <div class="icon"><svg width="24" height="22"><path d="M2 11 12 2l10 9H19v10H5V11z" fill="#fff"/></svg></div>
    <div><h3>Retail Malls</h3><p>Lorem ipsum dolor sit amet, consectetur adipisc-ing elit, sed do eiusmod tempor incididunt ut</p></div>
  </div>
  <div class="cat abs" style="left:361px;top:38px;display:flex;gap:18px">
    <div class="icon"><svg width="26" height="22"><circle cx="9" cy="7" r="4" fill="#fff"/><path d="M2 21c0-6 3-8 7-8s7 2 7 8z" fill="#fff"/><circle cx="18" cy="6" r="3" fill="#fff"/><path d="M17 12c4 0 7 2 7 7h-6" fill="#fff"/></svg></div>
    <div><h3>Shopping Complexes</h3><p>Lorem ipsum dolor sit amet, consectetur adipisc-ing elit, sed do eiusmod tempor incididunt ut</p></div>
  </div>
  <div class="cat abs" style="left:610px;top:38px;display:flex;gap:18px">
    <div class="icon"><svg width="26" height="22"><rect x="2" y="8" width="6" height="13" fill="#fff"/><rect x="10" y="3" width="6" height="18" fill="#fff"/><rect x="18" y="8" width="6" height="13" fill="#fff"/></svg></div>
    <div><h3>High Street Shops</h3><p>Lorem ipsum dolor sit amet, consectetur adipisc-ing elit, sed do eiusmod tempor incididunt ut</p></div>
  </div>
  <div class="cat abs" style="left:861px;top:38px;display:flex;gap:18px">
    <div class="icon"><svg width="24" height="24"><rect x="4" y="3" width="9" height="19" fill="#fff"/><rect x="14" y="9" width="6" height="13" fill="#fff"/></svg></div>
    <div><h3>Retail Warehouses</h3><p>Lorem ipsum dolor sit amet, consectetur adipisc-ing elit, sed do eiusmod tempor incididunt ut</p></div>
  </div>
</section>

<section class="featured" style="top:888px;height:459px">
  <h2 class="sec-title abs" style="left:123px;top:22px">Featured Retail Projects <small>Across India</small></h2>
  <div class="arrow abs" style="left:80px;top:160px"><svg width="8" height="12"><path d="M7 1 2 6l5 5" fill="none" stroke="#333" stroke-width="2"/></svg></div>
  <div class="arrow abs" style="left:1088px;top:160px"><svg width="8" height="12"><path d="M1 1l5 5-5 5" fill="none" stroke="#333" stroke-width="2"/></svg></div>

  <article class="card abs" style="left:125px;top:80px">
    <div class="photo" role="img" aria-label="Modern glass commercial tower" style="background:linear-gradient(160deg,#b9d7ef,#6f9cc4 55%,#5c7f5a)"><span class="tag deal">SALE</span><span class="tag kind">Shop Mall</span></div>
    <h4>Corvell Trinity</h4><div class="place">Gurgaon</div>
    <div class="row"><span>Dwarka Expressway</span><b>Shopping Complex</b></div>
    <div class="foot"><span class="price">$56000</span><span class="btn">View the listing</span></div>
  </article>
  <article class="card abs" style="left:454px;top:80px">
    <div class="photo" role="img" aria-label="Shopping mall exterior at dusk" style="background:linear-gradient(180deg,#5d8ed0,#9bb8d8 50%,#6f6a5e)"><span class="tag deal">SALE</span><span class="tag kind">Resturent</span></div>
    <h4>Mysore</h4><div class="place">Lakeway Mall</div>
    <div class="row"><span>Hunsur Main Road</span><b>Retail Malls</b></div>
    <div class="foot"><span class="price">$ 12300</span><span class="btn">View the listing</span></div>
  </article>
  <article class="card abs" style="left:788px;top:80px">
    <div class="photo" role="img" aria-label="Large shopping complex facade" style="background:linear-gradient(180deg,#c7d6e6,#8d7a70 55%,#6d6760)"><span class="tag deal">SALE</span><span class="tag kind">Tidal One</span></div>
    <h4>Noida</h4><div class="place">Tidal One</div>
    <div class="row"><span>NH Bypass</span><b>Shopping Complex</b></div>
    <div class="foot"><span class="price">$ 45600</span><span class="btn">View the listing</span></div>
  </article>
</section>

<section class="featured white" style="top:1347px;height:516px">
  <h2 class="sec-title abs" style="left:123px;top:42px">Featured Retail Projects <small>Across India</small></h2>
  <div class="arrow abs" style="left:78px;top:183px"><svg width="8" height="12"><path d="M7 1 2 6l5 5" fill="none" stroke="#333" stroke-width="2"/></svg></div>
  <div class="arrow abs" style="left:1091px;top:183px"><svg width="8" height="12"><path d="M1 1l5 5-5 5" fill="none" stroke="#333" stroke-width="2"/></svg></div>

  <article class="card abs" style="left:126px;top:97px">
    <div class="photo" role="img" aria-label="Mall exterior lit at night" style="background:linear-gradient(180deg,#2e3f63,#7e7d86 55%,#a58a5a)"><span class="tag deal">RENT</span><span class="tag kind">Resturent</span></div>
    <h4>Bhopal</h4><div class="place">The Grand Bazaar Place</div>
    <div class="row"><span>Klora Road</span><b>Retail Mall</b></div>
    <div class="foot"><span class="price">$ 13230</span><span class="btn">View the listing</span></div>
  </article>
  <article class="card abs" style="left:457px;top:97px">
    <div class="photo" role="img" aria-label="Curved glass mall building" style="background:linear-gradient(180deg,#3d5a8a,#9fb2c6 50%,#707a82)"><span class="tag deal">RENT</span><span class="tag kind">Shop Mall</span></div>
    <h4>Chennai</h4><div class="place">The Crestline Mall</div>
    <div class="row"><span>Velacheri</span><b>Retail Mall</b></div>
    <div class="foot"><span class="price">$ 13230</span><span class="btn">View the listing</span></div>
  </article>
  <article class="card abs" style="left:791px;top:97px">
    <div class="photo" role="img" aria-label="Glass office and retail tower" style="background:linear-gradient(180deg,#e9f0f6,#9fb8cf 50%,#4f6f7a)"><span class="tag deal">RENT</span><span class="tag kind">Tidal One</span></div>
    <h4>Gugaon</h4><div class="place">Orvane Skyline Road</div>
    <div class="row"><span>Golf Course</span><b>Shopping Complex</b></div>
    <div class="foot"><span class="price">$ 13230</span><span class="btn">View the listing</span></div>
  </article>
</section>

<section class="lower">
  <div class="abs" style="left:109px;top:40px;width:301px;height:330px">
    <h2 class="col-title">Listing Alert</h2>
    <div style="display:flex;gap:10px;margin-top:10px">
      <svg width="72" height="52" viewBox="0 0 72 52"><rect x="2" y="6" width="66" height="44" fill="#eee" stroke="#bbb"/><path d="M2 6l33 24L68 6" fill="none" stroke="#aaa" stroke-width="2"/></svg>
      <p class="note" style="line-height:18px;color:#555">Subscribe for Fortnightly Email update on New Listing @LotStallMart</p>
    </div>
    <div class="input" style="margin-top:16px">Enter your Email adress</div>
    <div class="input" style="margin-top:14px;color:var(--blue)">Select option<svg class="abs" style="right:8px;top:9px" width="8" height="10"><path d="M0 4 4 0l4 4M0 6l4 4 4-4" fill="#666"/></svg></div>
    <div class="note" style="margin-top:6px">(Select retail formate of intrest)</div>
    <div class="input" style="margin-top:8px"><span class="abs" style="right:0;top:0;width:18px;height:26px;background:#555"></span></div>
    <div class="note" style="margin-top:6px">(Select cities of Intrest)</div>
    <div class="btn abs" style="left:210px;top:286px;width:91px;height:30px;font-size:14px">Subscribe</div>
  </div>

  <div class="abs" style="left:440px;top:40px;width:307px;height:330px">
    <h2 class="col-title">Editor's Choice</h2>
    <div role="img" aria-label="Shoppers with bags beside a sale sign" style="margin-top:16px;width:305px;height:105px;background:linear-gradient(90deg,#7a3a2a,#c9924e 45%,#8a6a70)"></div>
    <p style="font-size:12.5px;line-height:17.5px;margin-top:16px">A "Select" Listing of Retail Properties Handpicked by our Editors based on their own positive evaluation on parameters &amp; attributes such as Design Concept, Location, Developer, Success Potential. So Read On to Check Out for yourself ............</p>
    <div class="btn abs" style="left:225px;top:286px;width:80px;height:30px;font-size:14px">More</div>
  </div>

  <div class="wizard-panel abs">
    <h2>Mart Wizards</h2>
    <p>Post your Retail Space requirement with us and our experts shall get back with suitable options and even help you in your transaction. This is a Free Service!</p>
    <div class="input">Enter your email address:</div>
    <div class="input">Mobile</div>
    <div class="input" style="height:61px;align-items:flex-start;padding-top:6px">Add Description of Requirment</div>
    <div class="btn abs" style="left:224px;top:304px;width:84px;height:26px;font-size:14px">Send</div>
  </div>
</section>

<footer class="site-footer">
  <h3 class="foot-title abs" style="left:110px;top:34px">ABOUT RETAIL CENTER</h3>
  <ul class="abs" style="left:110px;top:78px;line-height:40px">
    <li>About Us</li><li>Privacy Policy</li><li>terms of Uses</li><li>Contact Us</li><li>Site Map</li>
  </ul>
  <ul class="abs" style="left:260px;top:78px;line-height:40px">
    <li>Retail Malls</li><li>Shopping Complex</li><li>High Street Shops</li><li>Retail Warehouse</li>
  </ul>

  <h3 class="foot-title abs" style="left:453px;top:34px">www.Lotstallmart.com</h3>
  <p class="foot-text abs" style="left:453px;top:70px">LotStallMart.com - About Us LotStallMart.com is a Specialised Web based platform for Retail Space, featuring properties across India under various formats such as Retail Malls, Shopping Complexes, High-street Shops. Also featured are Retail Warehouses which provide the logistic back-end for the retail business. LotStallMart.com is useful to various category of users as follows- a. Devel <span style="color:#f5c76a">More...</span></p>

  <h3 class="foot-title abs" style="left:826px;top:34px">CONTACT INFO</h3>
  <div class="contact abs" style="left:826px;top:76px;width:280px">
    <p>214, C Block, Elm Street, London, BCA, United Kingdom</p>
    <p><svg width="12" height="12"><path d="M2 1h3l1 3-2 1c1 2 2 3 4 4l1-2 3 1v3c-6 0-10-4-10-10z" fill="#fff"/></svg>Phone : 1800-400-517-68</p>
    <p><svg width="12" height="10"><rect x=".5" y=".5" width="11" height="9" fill="none" stroke="#fff"/><path d="M1 1l5 4 5-4" fill="none" stroke="#fff"/></svg>Email : realestate@lotstallmail.com</p>
    <p><svg width="12" height="12"><circle cx="6" cy="6" r="5" fill="none" stroke="#fff"/><path d="M1 6h10M6 1v10" stroke="#fff"/></svg>Website : lotstallmart.com</p>
  </div>

  <p class="copy abs" style="left:110px;top:307px">Copyright © 2015 lotstallmart.com. All rights reserved.</p>
  <div class="brand foot-brand abs" style="left:819px;top:278px"><span class="dot"></span>lotstallmart</div>
</footer>

</body>
</html>
```